Upmarket Dessert Lounge needs a Business Card Design

We are an upmarket dessert lounge needing a business card to match our image.

We want something that is simple yet beautiful, feminine, classy, sophisticated and elegant. We want it to stand out and don't mind if it is bold.

The design should include our logo and colours of red or maroon with gold highlights. We don't mind if black is used.

Marlow & Quince

Target Market(s)

For those who like to indulge or treat themselves and give in to their temptations on good quality desserts.

Industry/Entity Type

Business

Requirements
Must have
• Must include our logo and our name

Marlow & Quince

M & Q

```html
<!DOCTYPE html>
<html lang="en">
<head>
<meta charset="utf-8">
<title>Marlow &amp; Quince — Business Card</title>
<link href="https://fonts.googleapis.com/css2?family=Cormorant+Garamond:wght@400;500&family=Tinos&display=swap" rel="stylesheet">
<style>
  :root {
    --backdrop: #3a3a3a;
    --maroon: #7f161a;
    --maroon-deep: #6c1115;
    --gold: #f6d9a0;
    --gold-soft: rgba(246, 217, 160, 0.28);
  }
  * { margin: 0; padding: 0; box-sizing: border-box; }
  html, body {
    width: 1200px; height: 900px; overflow: hidden;
    background: var(--backdrop);
  }
  .canvas { position: relative; width: 1200px; height: 900px; }
  .card {
    position: absolute; top: 308px;
    width: 514px; height: 282px;
    border-radius: 24px;
    background: var(--maroon);
    overflow: hidden;
    color: var(--gold);
  }
  .card--front { left: 73px; }
  .card--back { left: 616px; }

  .damask-field {
    position: absolute; inset: 0;
    background: radial-gradient(ellipse at 50% 45%, var(--maroon) 30%, var(--maroon-deep) 100%);
  }
  .brand-name {
    position: absolute; left: 0; right: 0; top: 122px;
    text-align: center;
    font-family: "Cormorant Garamond", serif;
    font-weight: 400; font-size: 34px; letter-spacing: 1px;
    text-transform: uppercase;
  }
  .tagline {
    position: absolute; left: 0; right: 0; top: 249px;
    text-align: center;
    font-family: "Tinos", serif;
    font-size: 11px; letter-spacing: 4px;
    text-transform: uppercase;
  }

  .side-flourish {
    position: absolute; top: 28px;
    width: 68px; height: 227px;
    border-radius: 30px;
    background: linear-gradient(180deg, var(--gold-soft), rgba(246,217,160,0.12), var(--gold-soft));
  }
  .side-flourish--left { left: 23px; }
  .side-flourish--right { right: 24px; }
  .monogram {
    position: absolute; left: 0; right: 0; top: 64px;
    text-align: center;
    font-family: "Cormorant Garamond", serif;
    font-weight: 400; font-size: 60px; line-height: 1;
  }
  .contact {
    position: absolute; left: 0; right: 0; top: 188px;
    text-align: center; list-style: none;
    font-family: "Tinos", serif;
    font-size: 12.5px; line-height: 15.5px;
  }
</style>
</head>
<body>
<main class="canvas">
  <section class="card card--front" aria-label="Card front">
    <div class="damask-field" role="img" aria-label="Faint tone-on-tone damask flourish pattern"></div>
    <h1 class="brand-name">Marlow &amp; Quince</h1>
    <p class="tagline">Upmarket Dessert Lounge</p>
  </section>

  <section class="card card--back" aria-label="Card back">
    <div class="side-flourish side-flourish--left" role="img" aria-label="Gold vertical scroll ornament"></div>
    <div class="side-flourish side-flourish--right" role="img" aria-label="Gold vertical scroll ornament"></div>
    <p class="monogram">M&amp;Q</p>
    <ul class="contact">
      <li>Harrow Bay, South Australia</li>
      <li>555 010 20 30</li>
      <li>info@marlow-quince.com | www.marlow-quince.com</li>
      <li>www.marlowquince.social/lounge</li>
    </ul>
  </section>
</main>
</body>
</html>
```